Business card design/logo/website name

I am a business coach. My business name is KDP (Kessel Dunmore & Partners, Inc.) I want to use this card just for coaching. I do two kinds: Personal Image coach and Executive business coach
1. I work with people to become a polished global professional.
"Become a confident, savvy professional building relationships tactfully and appropriately while clearly representing your own company’s message and image.
Learn the nuances… Master the skills… Use the business etiquette techniques and protocols that allow you to seamlessly and confidently conduct business in a global business environment.
Have the comfort of knowing what to expect, what to do and how to easily build long and short-term relationships that give you the winning edge and increased company profits."
2. Leadership Coaching
For increasing the team’s productivity by building stronger relationships. Build strong compelling vision and write and share their Personal Leadership Philosophy, a roadmap that is concise and commanding and gives the team a clear vision of the leader's expectations.
Updates

KDP should be the logo. (Downplay the Kessel Dunmore and Partners, Inc.)

Want:
Executive Coach
Consultant

Reason: I am traveling and connections are often broken.

Target Market(s)

Executives, business people

Industry/Entity Type

Building

Font styles to use
Sans Serif
Script

Colors
0255a3
3176b5
85acd3
ec2027

Requirements
Must have
• KDP as the logo,(no preference on how you treat KDP) with Kessel Dunmore & Partners. Inc. downplayed.
On the card:
Rosalind Dunmore CEO
Executive Coach
Consultant
KRC 4(c)
Coaching - Training - Strategic Planning

```html
<!DOCTYPE html>
<html lang="en">
<head>
<meta charset="utf-8">
<title>Kessel Dunmore &amp; Partners – Business Card</title>
<link rel="stylesheet" href="https://fonts.googleapis.com/css2?family=Arimo:wght@400;700&display=swap">
<style>
  :root{
    --backdrop:#2f3f3f;
    --card:#ffffff;
    --brand-deep:#0255a3;
    --band-light:#6a98d4;
    --band-mid:#3a6fb8;
    --band-dark:#1f4a8f;
    --ink:#0b4d96;
    --ink-soft:#2a5f9e;
    --pattern-a:#eef1f5;
    --pattern-b:#ffffff;
  }
  *{box-sizing:border-box;margin:0;padding:0}
  html,body{width:1200px;height:1000px;overflow:hidden}
  body{
    background:var(--backdrop);
    font-family:"Arimo",Arial,sans-serif;
    position:relative;
  }
  .card{
    position:absolute;
    width:525px;height:300px;
    background:var(--card);
    overflow:hidden;
    box-shadow:0 10px 26px rgba(0,0,0,.45);
  }
  .card--front{left:50px;top:350px}
  .card--back{left:625px;top:350px}
  .card__bands{position:absolute;inset:0;width:100%;height:100%}
  .card__pattern{
    position:absolute;border-radius:50%;
    background:radial-gradient(circle,var(--pattern-a) 0%,var(--pattern-b) 70%);
  }
  .card--front .card__pattern{width:220px;height:220px;left:150px;top:30px}
  .card--back .card__pattern{width:230px;height:230px;left:148px;top:10px}

  .wordmark{position:absolute;color:var(--brand-deep);font-weight:700;line-height:1}
  .wordmark__mark{display:block;letter-spacing:2px}
  .wordmark__legal{display:block;font-weight:400;letter-spacing:.3px}
  .card--front .wordmark{left:30px;top:32px}
  .card--front .wordmark__mark{font-size:46px}
  .card--front .wordmark__legal{font-size:7.5px;margin-top:4px}
  .card--back .wordmark{left:0;right:0;top:62px;text-align:center}
  .card--back .wordmark__mark{font-size:84px;letter-spacing:5px}
  .card--back .wordmark__legal{font-size:10px;margin-top:6px}

  .details{position:absolute;left:30px;top:112px;color:var(--ink)}
  .details__name{font-size:19px;font-weight:700}
  .details__title{font-size:14px;margin-top:3px}
  .details__services{font-size:12.5px;margin-top:12px}
  .contact{list-style:none;margin-top:8px;font-size:11.5px;color:var(--ink-soft)}
  .contact li{display:flex;align-items:flex-start;gap:7px;margin-top:3px;line-height:1.25}
  .contact svg{width:10px;height:10px;flex:none;margin-top:2px;fill:var(--ink)}
</style>
</head>
<body>

<section class="card card--front" aria-label="Card front">
  <svg class="card__bands" viewBox="0 0 525 300" aria-hidden="true">
    <polygon points="345,0 525,0 525,300 470,300" fill="var(--band-light)"/>
    <polygon points="378,0 525,0 525,300 500,300" fill="var(--band-mid)"/>
    <polygon points="415,0 525,0 525,200" fill="var(--band-dark)"/>
  </svg>
  <div class="card__pattern" role="img" aria-label="Faint guilloche rosette pattern"></div>

  <div class="wordmark">
    <span class="wordmark__mark">KDP</span>
    <span class="wordmark__legal">KESSEL DUNMORE &amp; PARTNERS, INC</span>
  </div>

  <div class="details">
    <p class="details__name">Rosalind L. Dunmore, CEO</p>
    <p class="details__title">Global Executive Coach</p>
    <p class="details__services">Training, Coaching, Diversity, Protocol</p>
    <ul class="contact">
      <li><svg viewBox="0 0 10 10"><path d="M5 0 10 5H8.5V10H6V7H4V10H1.5V5H0Z"/></svg><span>2240 Harbor Ridge Ln, Marlow,<br>FL 32990, United States</span></li>
      <li><svg viewBox="0 0 10 10"><path d="M2 0 4 2.5 3 4Q4 6 6 7L7.5 6 10 8 8.5 10Q4 10 0 2Z"/></svg><span>(555) 310.2847</span></li>
      <li><svg viewBox="0 0 10 10"><path d="M0 1.5H10V8.5H0Z M0.8 2.2 5 5.5 9.2 2.2" stroke="#fff" stroke-width=".8"/></svg><span>rdunmore@kesseldunmore.com</span></li>
      <li><svg viewBox="0 0 10 10"><path d="M1 6 4 3 5 4 2.5 6.5 3.5 7.5 6 5 7 6 4 9Z M6 1 9 4 7.5 5.5 6.5 4.5 7.5 3.5 6.5 2.5 5.5 3.5 4.5 2.5Z"/></svg><span>kesseldunmore.com</span></li>
    </ul>
  </div>
</section>

<section class="card card--back" aria-label="Card back">
  <div class="card__pattern" role="img" aria-label="Faint guilloche rosette pattern"></div>
  <svg class="card__bands" viewBox="0 0 525 300" aria-hidden="true">
    <polygon points="0,205 525,165 525,300 0,300" fill="var(--band-light)"/>
    <polygon points="0,228 525,198 525,300 0,300" fill="var(--band-mid)"/>
    <polygon points="0,248 525,300 0,300" fill="var(--band-dark)"/>
  </svg>
  <div class="wordmark">
    <span class="wordmark__mark">KDP</span>
    <span class="wordmark__legal">KESSEL DUNMORE &amp; PARTNERS, INC</span>
  </div>
</section>

</body>
</html>
```